Vorn upkeep KT Solar Venture

Solar power system install
Services and maintenance
wiring, Rewinding and Renovation
Switch Board Upgrade
Power and lighting point
t doesn’t matter how much you spend on quality parts, your solar system will let you down if your design and installation are sub-par. Have your solar system tailored and installed by our Master Electrician and Bright Grid Guild Accredited team.

Target Market(s)

sales and installed

Industry/Entity Type

Solar install and retailer

Contact Information for Business Card

Name , Email, Phone Number ,Business address,

Font styles to use
Serif

Colors
0054AA
0677BA
7BADD7
CADEEF
E8F1F8

Requirements
Must have
• clear and bright
Nice to have
• new design
Should not have
• unclear pictures

```html
<!DOCTYPE html>
<html lang="en">
<head>
<meta charset="utf-8">
<title>Vorn upkeep – Business Card</title>
<link rel="stylesheet" href="https://fonts.googleapis.com/css2?family=Roboto:wght@400;500&display=swap">
<style>
  :root {
    --page-bg: #e4e8ed;
    --card-bg: #f5f8fb;
    --brand-deep: #0054AA;
    --brand-mid: #0677BA;
    --brand-soft: #7BADD7;
    --brand-pale: #CADEEF;
    --brand-mist: #E8F1F8;
    --leaf-green: #2f9e3a;
    --ink: #1d2228;
    --contact-ink: #f1f5f9;
  }
  html, body {
    margin: 0;
    width: 1200px;
    height: 1054px;
    overflow: hidden;
    background: var(--page-bg);
  }
  .business-card {
    position: absolute;
    left: 100px;
    top: 224px;
    width: 1000px;
    height: 606px;
    border-radius: 24px;
    background: var(--card-bg);
    overflow: hidden;
    box-shadow: 0 18px 40px rgba(20, 40, 70, 0.18);
    font-family: "Roboto", Arial, sans-serif;
  }
  .accent-band {
    position: absolute;
    left: 0;
    right: 0;
    bottom: 0;
    height: 206px;
    background: linear-gradient(180deg, var(--brand-soft) 0%, var(--brand-mid) 35%, var(--brand-deep) 100%);
    border-top: 8px solid var(--leaf-green);
  }
  .brand-block {
    position: absolute;
    left: 46px;
    top: 110px;
    width: 440px;
    display: flex;
    align-items: center;
    gap: 22px;
  }
  .brand-dot {
    flex: none;
    width: 64px;
    height: 64px;
    border-radius: 50%;
    background: var(--brand-pale);
  }
  .brand-name {
    margin: 0;
    font-family: "Roboto", Arial, sans-serif;
    font-weight: 500;
    color: var(--brand-deep);
    font-size: 34px;
    line-height: 42px;
  }
  .person-block {
    position: absolute;
    right: 46px;
    top: 64px;
    text-align: right;
    color: var(--ink);
  }
  .person-name {
    margin: 0;
    font-weight: 500;
    font-size: 39px;
    color: var(--brand-deep);
    line-height: 46px;
  }
  .person-role {
    margin: 4px 0 0;
    font-weight: 400;
    font-size: 25px;
    line-height: 30px;
  }
  .person-address {
    margin: 34px 0 0;
    font-style: normal;
    font-size: 26px;
    line-height: 38px;
  }
  .contact-list {
    position: absolute;
    right: 46px;
    top: 436px;
    margin: 0;
    padding: 0;
    list-style: none;
    color: var(--contact-ink);
    font-size: 26px;
  }
  .contact-item {
    display: flex;
    justify-content: flex-end;
    align-items: center;
    height: 38px;
  }
  .contact-icon {
    width: 22px;
    height: 22px;
    margin-left: 24px;
  }
</style>
</head>
<body>
  <article class="business-card">
    <div class="accent-band" role="img" aria-label="Decorative blue and green wave band with small wind turbines"></div>

    <header class="brand-block">
      <div class="brand-dot"></div>
      <h1 class="brand-name">Vorn upkeep<br>KT Solar Venture</h1>
    </header>

    <section class="person-block">
      <h2 class="person-name">Mara Ellison</h2>
      <p class="person-role">Managing Director</p>
      <address class="person-address">234 Anywhere St., Any City,<br>Any Town, US 123456</address>
    </section>

    <ul class="contact-list">
      <li class="contact-item">828-555-0142
        <svg class="contact-icon" viewBox="0 0 24 24"><path fill="currentColor" d="M3 9c0-3 4-5 9-5s9 2 9 5v2h-5V9H8v2H3z M6 12h12l2 8H4z"/><circle cx="12" cy="16" r="2" fill="var(--brand-mid)"/></svg>
      </li>
      <li class="contact-item">mara@vornupkeep.com
        <svg class="contact-icon" viewBox="0 0 24 24"><rect x="2" y="5" width="20" height="14" fill="currentColor"/><path d="M2 5l10 8 10-8" fill="none" stroke="var(--brand-mid)" stroke-width="2"/></svg>
      </li>
      <li class="contact-item">www.vornupkeep.com
        <svg class="contact-icon" viewBox="0 0 24 24"><circle cx="12" cy="12" r="10" fill="currentColor"/><g fill="none" stroke="var(--brand-mid)" stroke-width="1.5"><ellipse cx="12" cy="12" rx="4" ry="10"/><path d="M2 12h20M4 7h16M4 17h16"/></g></svg>
      </li>
    </ul>
  </article>
</body>
</html>
```